Harborline Outpost Registry needs a web design

We are launching a new website and need a web design. The website is going to list every military base and installment around the world with information on each base such as a description of the base, the history of the base, contact information at the base, address, lat/long of the base, and any other relevant information including images of the base. We need a home page with navigation menu and the design of the military base page so that every military base page is formatted the same for the referenced information. We have included an example of the content that may be found on the base page(s). We are also going to have the information available in spanish.

We also wanted to mention we will be building this website in wordpress.

We also wanted to note that in the format of each base page, we will have a frequently asked questions section with answers.

```html
<!DOCTYPE html>
<html lang="en">
<head>
<meta charset="utf-8">
<title>Harborline Outpost Registry</title>
<link href="https://fonts.googleapis.com/css2?family=Barlow:ital,wght@0,400;0,500;0,600;0,700;1,400;1,500&family=Poppins:wght@700;800&family=Roboto:wght@400;500&display=swap" rel="stylesheet">
<style>
:root{
  --green:#479c80;
  --green-soft:#5fae93;
  --ink:#1f1f1f;
  --muted:#555;
  --footer:#262626;
  --white:#fff;
  --star:#f5b800;
  --line:#d9d9d9;
}
*{box-sizing:border-box;margin:0;padding:0}
html,body{width:1200px;height:2539px;overflow:hidden}
body{position:relative;font-family:'Barlow',sans-serif;color:var(--ink);background:var(--white)}
.abs{position:absolute}

/* hero */
.hero{left:0;top:0;width:1200px;height:728px;
  background:
   radial-gradient(ellipse at 50% 55%,rgba(0,0,0,.05),rgba(0,0,0,.6)),
   linear-gradient(180deg,#3a1f25 0%,#6e2630 25%,#8a2f35 45%,#4a2226 70%,#2a1a1c 100%);}
.topbar{left:0;top:0;width:1200px;height:85px;background:rgba(20,14,16,.55)}
.brand{left:112px;top:14px;color:var(--white);font-weight:700;font-size:25px;line-height:30px}
.nav{left:446px;top:32px;display:flex;gap:29px;font-weight:500;font-size:15px;color:var(--white)}
.nav .active{color:#6cc3a5;position:relative}
.nav .active::after{content:"";position:absolute;left:-3px;right:-4px;top:48px;height:3px;background:var(--green)}
.top-search{left:850px;top:32px;color:var(--white);font-weight:500;font-size:15px;display:flex;gap:18px;align-items:center}
.quote{left:975px;top:22px;width:114px;height:41px;background:var(--green);color:var(--white);font-weight:700;font-size:14px;display:flex;align-items:center;justify-content:center}
.follow{left:50px;top:262px;width:14px;height:100px;color:var(--white);font-size:10px;letter-spacing:2.5px;font-family:'Roboto',sans-serif;writing-mode:vertical-rl;transform:rotate(180deg);text-align:right}
.follow-line{left:57px;top:372px;width:1px;height:62px;background:var(--white)}
.social-dot{left:53px;width:9px;height:9px;background:var(--white);border-radius:50%}
.hero-title{left:0;top:238px;width:1200px;text-align:center;color:var(--white);font-family:'Poppins',sans-serif;font-weight:800;font-size:61px;line-height:68px}
.locate{left:322px;top:386px;width:556px;height:55px;background:var(--white);display:flex;align-items:center}
.locate .hint{margin-left:48px;font-size:14px;color:#666}
.locate .go{position:absolute;right:7px;top:7px;width:132px;height:41px;background:var(--green);color:var(--white);font-weight:700;font-size:15px;display:flex;align-items:center;justify-content:center;gap:6px}

/* categories */
.cats{left:113px;top:633px;display:flex;gap:14px}
.cat{width:184px;height:184px;background:var(--green);color:var(--white);display:flex;flex-direction:column;align-items:center;padding-top:28px}
.cat .art{width:86px;height:86px;background:var(--green-soft);border-radius:4px}
.cat span{margin-top:16px;font-weight:600;font-size:18px}

/* popular */
.h2{left:0;width:1200px;text-align:center;font-family:'Poppins',sans-serif;font-weight:700;font-size:42px}
.cards{left:113px;top:1001px;display:flex;gap:28px}
.card{width:307px;height:500px;border:1px solid var(--line);background:var(--white)}
.photo{height:242px}
.p1{background:linear-gradient(180deg,#e9a44a 0%,#c27a55 35%,#4b6f95 60%,#2e4f78 100%)}
.p2{background:linear-gradient(160deg,#b8c3c9 0%,#7e8c93 45%,#3d4449 100%)}
.p3{background:linear-gradient(180deg,#d5dde2 0%,#8e9aa0 40%,#5f9a45 70%,#3f7a2c 100%)}
.card-body{padding:22px 27px 0}
.card h3{font-weight:600;font-size:20px}
.stars{margin-top:14px;display:flex}
.card .sub{margin-top:12px;font-size:14px;color:var(--muted)}
.row{margin-top:13px;font-size:14px;color:#333;display:flex;align-items:flex-start;line-height:21px;white-space:nowrap}
.row svg{margin:4px 6px 0 0;flex:none}
.row .lbl{color:var(--muted);margin-right:8px}
.row .val{font-weight:500}
.links{display:flex;justify-content:space-between;margin-top:14px;font-weight:600;font-size:14px;color:var(--green);text-decoration:underline}
.arrow{width:40px;height:40px;border-radius:50%;background:var(--white);box-shadow:0 2px 8px rgba(0,0,0,.15);display:flex;align-items:center;justify-content:center;top:1233px}

/* reviews */
.reviews{left:0;top:1603px;width:1200px;height:507px;background:var(--green)}
.reviews .h2{color:var(--white);top:98px;font-size:44px}
.review{top:183px;width:445px;color:var(--white)}
.review .head{display:flex;justify-content:space-between;align-items:center}
.review .name{font-weight:600;font-size:18px}
.review p{margin-top:14px;font-style:italic;font-size:14px;line-height:21.5px;text-align:justify}
.review .meta{margin-top:18px;display:flex;gap:44px;font-size:14px;align-items:center}
.review .meta span{display:flex;gap:4px;align-items:center}
.quote-mark{position:absolute;right:0;top:154px;width:44px;height:32px}
.dots{left:578px;top:422px;display:flex;gap:6px}
.dots i{width:10px;height:10px;border-radius:50%;background:rgba(255,255,255,.6)}
.dots i.on{background:var(--white)}

/* footer */
.footer{left:0;top:2110px;width:1200px;height:429px;background:var(--footer);color:var(--white);font-family:'Roboto',sans-serif}
.footer .brand{top:100px;left:112px;font-family:'Barlow',sans-serif}
.f-social{left:112px;top:188px;display:flex;gap:8px}
.f-social i{width:33px;height:35px;background:var(--white)}
.f-h{font-family:'Barlow',sans-serif;font-weight:600;font-size:21px;top:102px}
.f-list{top:146px;left:397px;list-style:none;font-size:16px;line-height:28.5px}
.f-list li::before{content:"»";margin-right:10px}
.contact{left:577px;top:146px;font-size:16px}
.contact .c{display:flex;gap:12px;line-height:28px}
.field{left:823px;width:265px;height:41px;background:var(--white);color:#888;font-size:12px;padding-left:13px;display:flex;align-items:center}
.submit{left:820px;top:2390px;width:109px;height:42px;border-radius:21px;background:var(--green);font-size:14px;display:flex;align-items:center;justify-content:center;color:var(--white);font-weight:700}
.f-rule{left:112px;top:2466px;width:977px;height:1px;background:#555}
.copy{left:0;top:2488px;width:1200px;text-align:center;font-size:14px;color:var(--white);font-family:'Roboto',sans-serif}
</style>
</head>
<body>
<svg width="0" height="0" style="position:absolute">
  <defs>
    <path id="star" d="M6.5 1l1.6 3.6 3.9.4-2.9 2.6.8 3.9-3.4-2-3.4 2 .8-3.9L1 5l3.9-.4z"/>
    <path id="pin" d="M5 0a5 5 0 0 1 5 5c0 4-5 9-5 9S0 9 0 5a5 5 0 0 1 5-5z"/>
    <path id="phone" d="M5 2l4 1 1 5-2 2q2 4 6 6l2-2 5 1 1 4-3 3Q6 21 2 5z"/>
  </defs>
</svg>

<section class="abs hero" role="img" aria-label="Silhouettes of soldiers in front of a waving American flag"></section>
<div class="abs topbar"></div>
<div class="abs brand">Harborline<br>Outpost Registry</div>
<nav class="abs nav"><span class="active">Home</span><span>About</span><span>Services</span><span>Blog</span><span>Contact</span></nav>
<div class="abs top-search">
  <svg width="14" height="14" viewBox="0 0 14 14"><circle cx="6" cy="6" r="4.5" fill="none" stroke="#fff" stroke-width="2"/><path d="M9.5 9.5L13 13" stroke="#fff" stroke-width="2"/></svg>
  <span>Search</span>
</div>
<div class="abs quote">GET A QUOTE</div>

<div class="abs follow">FOLLOW US</div>
<div class="abs follow-line"></div>
<div class="abs social-dot" style="top:459px"></div>
<div class="abs social-dot" style="top:489px"></div>
<div class="abs social-dot" style="top:520px"></div>

<h1 class="abs hero-title">US MILITARY<br>BASE DIRECTORY</h1>
<div class="abs locate">
  <svg class="abs" style="left:20px;top:20px" width="10" height="14" viewBox="0 0 10 14"><use href="#pin" fill="#555"/><circle cx="5" cy="5" r="2" fill="#fff"/></svg>
  <span class="hint">Enter your location</span>
  <div class="go"><svg width="13" height="13" viewBox="0 0 14 14"><circle cx="6" cy="6" r="4.5" fill="none" stroke="#fff" stroke-width="2"/><path d="M9.5 9.5L13 13" stroke="#fff" stroke-width="2"/></svg>SEARCH</div>
</div>

<div class="abs cats">
  <div class="cat"><div class="art" role="img" aria-label="Line illustration of a barracks hut and watchtower"></div><span>Duis aute irure</span></div>
  <div class="cat"><div class="art" role="img" aria-label="Line illustration of a field tent with flag"></div><span>Duis aute irure</span></div>
  <div class="cat"><div class="art" role="img" aria-label="Line illustration of a lookout tower"></div><span>Duis aute irure</span></div>
  <div class="cat"><div class="art" role="img" aria-label="Line illustration of a uniformed service member"></div><span>Duis aute irure</span></div>
  <div class="cat"><div class="art" role="img" aria-label="Line illustration of a hand holding a rank shield"></div><span>Duis aute irure</span></div>
</div>

<h2 class="abs h2" style="top:910px">POPULAR THIS WEEK</h2>

<div class="abs arrow" style="left:37px"><svg width="10" height="12" viewBox="0 0 10 12"><path d="M7 1L2 6l5 5" fill="none" stroke="#222" stroke-width="1.8"/></svg></div>
<div class="abs arrow" style="left:1123px"><svg width="10" height="12" viewBox="0 0 10 12"><path d="M3 1l5 5-5 5" fill="none" stroke="#222" stroke-width="1.8"/></svg></div>

<div class="abs cards">
  <article class="card">
    <div class="photo p1" role="img" aria-label="Coastal hillside village with white buildings at sunset"></div>
    <div class="card-body">
      <h3>Fort Calder Military Base:</h3>
      <div class="stars"><svg width="80" height="13" viewBox="0 0 80 13"><g fill="none" stroke="#f5b800"><use href="#star"/><use href="#star" x="16"/><use href="#star" x="32"/><use href="#star" x="48"/><use href="#star" x="64"/></g></svg></div>
      <div class="sub">History, Facilities, and Support Services</div>
      <div class="row"><svg width="12" height="12" viewBox="0 0 24 24"><use href="#phone" fill="#479c80"/></svg><span class="lbl">Phone :</span><span class="val">(555) 014-2290</span></div>
      <div class="row"><svg width="9" height="13" viewBox="0 0 10 14"><use href="#pin" fill="#479c80"/><circle cx="5" cy="5" r="2" fill="#fff"/></svg><span class="lbl">Location :</span><span class="val">Calder Ridge, KY,<br>United States</span></div>
      <div class="links"><span>Directions</span><span>Email</span></div>
    </div>
  </article>
  <article class="card">
    <div class="photo p2" role="img" aria-label="Travellers walking through a modern airport terminal"></div>
    <div class="card-body">
      <h3>Fort Calder Military Base:</h3>
      <div class="stars"><svg width="80" height="13" viewBox="0 0 80 13"><g fill="none" stroke="#f5b800"><use href="#star"/><use href="#star" x="16"/><use href="#star" x="32"/><use href="#star" x="48"/><use href="#star" x="64"/></g></svg></div>
      <div class="sub">History, Facilities, and Support Services</div>
      <div class="row"><svg width="12" height="12" viewBox="0 0 24 24"><use href="#phone" fill="#479c80"/></svg><span class="lbl">Phone :</span><span class="val">(555) 014-2290</span></div>
      <div class="row"><svg width="9" height="13" viewBox="0 0 10 14"><use href="#pin" fill="#479c80"/><circle cx="5" cy="5" r="2" fill="#fff"/></svg><span class="lbl">Location :</span><span class="val">Calder Ridge, KY,<br>United States</span></div>
      <div class="links"><span>Directions</span><span>Email</span></div>
    </div>
  </article>
  <article class="card">
    <div class="photo p3" role="img" aria-label="City skyline behind green rooftop gardens"></div>
    <div class="card-body">
      <h3>Fort Calder Military Base:</h3>
      <div class="stars"><svg width="80" height="13" viewBox="0 0 80 13"><g fill="none" stroke="#f5b800"><use href="#star"/><use href="#star" x="16"/><use href="#star" x="32"/><use href="#star" x="48"/><use href="#star" x="64"/></g></svg></div>
      <div class="sub">History, Facilities, and Support Services</div>
      <div class="row"><svg width="12" height="12" viewBox="0 0 24 24"><use href="#phone" fill="#479c80"/></svg><span class="lbl">Phone :</span><span class="val">(555) 014-2290</span></div>
      <div class="row"><svg width="9" height="13" viewBox="0 0 10 14"><use href="#pin" fill="#479c80"/><circle cx="5" cy="5" r="2" fill="#fff"/></svg><span class="lbl">Location :</span><span class="val">Calder Ridge, KY,<br>United States</span></div>
      <div class="links"><span>Directions</span><span>Email</span></div>
    </div>
  </article>
</div>

<section class="abs reviews">
  <h2 class="abs h2">RECENT REVIEWS</h2>
  <div class="abs review" style="left:113px">
    <div class="head"><svg width="94" height="15" viewBox="0 0 94 15"><g fill="#f5b800" transform="scale(1.1)"><use href="#star"/><use href="#star" x="18"/><use href="#star" x="36"/><use href="#star" x="54"/><use href="#star" x="72"/></g></svg><span class="name">John Doe</span></div>
    <p>“Lorem ipsum dolor sit amet, consectetur adipiscing elit, sed do eiusmod tempor incididunt ut labore et dolore magna aliqua. Ut enim ad minim veniam, quis nostrud exercitation ullamco laboris nisi ut aliquip ex ea commodo consequat. Duis aute irure dolor in reprehenderit in voluptate velit esse cillum dolore eu fugiat nulla pariatur.”</p>
    <div class="meta">
      <span><svg width="13" height="13" viewBox="0 0 13 13"><rect x=".5" y="2" width="12" height="10.5" fill="none" stroke="#fff"/><path d="M.5 5h12" stroke="#fff"/></svg>Jan 22</span>
      <span><svg width="13" height="13" viewBox="0 0 13 13"><circle cx="6.5" cy="6.5" r="5.5" fill="none" stroke="#fff" stroke-width="1.5"/><path d="M6.5 3.5v3h2.5" fill="none" stroke="#fff" stroke-width="1.5"/></svg>10:48</span>
    </div>
    <svg class="quote-mark" viewBox="0 0 44 32"><g fill="rgba(255,255,255,.35)"><path d="M11 32a10 10 0 1 1 0-20c-1-5-4-8-8-9l2-3c10 3 16 11 16 22a10 10 0 0 1-10 10z"/><path d="M34 32a10 10 0 1 1 0-20c-1-5-4-8-8-9l2-3c10 3 16 11 16 22a10 10 0 0 1-10 10z"/></g></svg>
  </div>
  <div class="abs review" style="left:644px">
    <div class="head"><svg width="94" height="15" viewBox="0 0 94 15"><g fill="#f5b800" transform="scale(1.1)"><use href="#star"/><use href="#star" x="18"/><use href="#star" x="36"/><use href="#star" x="54"/><use href="#star" x="72"/></g></svg><span class="name">John Doe</span></div>
    <p>“Lorem ipsum dolor sit amet, consectetur adipiscing elit, sed do eiusmod tempor incididunt ut labore et dolore magna aliqua. Ut enim ad minim veniam, quis nostrud exercitation ullamco laboris nisi ut aliquip ex ea commodo consequat. Duis aute irure dolor in reprehenderit in voluptate velit esse cillum dolore eu fugiat nulla pariatur.”</p>
    <div class="meta">
      <span><svg width="13" height="13" viewBox="0 0 13 13"><rect x=".5" y="2" width="12" height="10.5" fill="none" stroke="#fff"/><path d="M.5 5h12" stroke="#fff"/></svg>Jan 22</span>
      <span><svg width="13" height="13" viewBox="0 0 13 13"><circle cx="6.5" cy="6.5" r="5.5" fill="none" stroke="#fff" stroke-width="1.5"/><path d="M6.5 3.5v3h2.5" fill="none" stroke="#fff" stroke-width="1.5"/></svg>10:48</span>
    </div>
    <svg class="quote-mark" viewBox="0 0 44 32"><g fill="rgba(255,255,255,.35)"><path d="M11 32a10 10 0 1 1 0-20c-1-5-4-8-8-9l2-3c10 3 16 11 16 22a10 10 0 0 1-10 10z"/><path d="M34 32a10 10 0 1 1 0-20c-1-5-4-8-8-9l2-3c10 3 16 11 16 22a10 10 0 0 1-10 10z"/></g></svg>
  </div>
  <div class="abs dots"><i></i><i class="on"></i><i></i></div>
</section>

<footer class="abs footer">
  <div class="abs brand">Harborline<br>Outpost Registry</div>
  <div class="abs f-social"><i></i><i></i><i></i><i></i></div>
  <div class="abs f-h" style="left:397px">Information</div>
  <ul class="abs f-list"><li>Home</li><li>Services</li><li>Features</li><li>About us</li><li>Blog</li><li>Contact us</li></ul>
  <div class="abs f-h" style="left:577px">Contact Us</div>
  <div class="abs contact">
    <div class="c"><svg width="20" height="20" viewBox="0 0 10 14"><use href="#pin" fill="#479c80"/><circle cx="5" cy="5" r="2" fill="#262626"/></svg><span>123, Lorem Ipsum<br>simply dummy</span></div>
    <div class="c" style="margin-top:29px"><svg width="22" height="22" viewBox="0 0 24 24"><use href="#phone" fill="#479c80"/></svg><span>+1 888 888 8888</span></div>
    <div class="c" style="margin-top:29px"><svg width="22" height="22" viewBox="0 0 24 24"><rect x="1" y="5" width="22" height="14" fill="#479c80"/><path d="M1 5l11 8 11-8" fill="none" stroke="#262626" stroke-width="1.5"/></svg><span>info@companyname.com</span></div>
  </div>
  <div class="abs f-h" style="left:822px">Newsletter</div>
</footer>
<div class="abs field" style="top:2262px">Your Name</div>
<div class="abs field" style="top:2313px">Enter Your Email Address</div>
<div class="abs submit">SUBMIT</div>
<div class="abs f-rule"></div>
<div class="abs copy">© Copyrights Company name 2023. All rights reserved | Privacy policy | Terms Condition</div>

</body>
</html>
```